Oil Field Service company needs professional business cards

Looking to clean up our current company business cards and look a little more professional. Brenwick Casing Services is a US based company that services the oil field. We deal with engineers, managers and oil rigs....................................................................................................................................................................................................................................................................................................................................................................................................

Target Market(s)

Oil and Gas professionals

Industry/Entity Type

Oil And Gas

Contact Information for Business Card

See attached photo as example

Font styles to use
Sans Serif

Colors
ec1f27

Requirements
Must have
• Company Logo, Name, Title, Cell, Office, Fax, Email.
• See attached photo
Nice to have
• External CRT, Internal CRT, Casing Crews, Torque Turn, Laydown Machine
Should not have
• Do not introduce any new pictures and keep it professional looking

```html
<!DOCTYPE html>
<html lang="en">
<head>
<meta charset="utf-8">
<title>Brenwick Casing Services – Business Card</title>
<link rel="stylesheet" href="https://fonts.googleapis.com/css2?family=Open+Sans:wght@400;600;700&display=swap">
<style>
  :root {
    --backdrop: #3b3430;
    --card-black: #050505;
    --card-glow: #2a2a2c;
    --brand-red: #ec1f27;
    --steel-grey: #5d6770;
    --text-white: #ffffff;
    --text-soft: #e6e6e6;
  }
  * { box-sizing: border-box; margin: 0; padding: 0; }
  html, body {
    width: 1200px;
    height: 844px;
    overflow: hidden;
    background: var(--backdrop);
    font-family: "Open Sans", Arial, sans-serif;
  }
  .stage {
    width: 1200px;
    height: 844px;
    display: flex;
    align-items: center;
    justify-content: center;
    gap: 60px;
  }
  .card {
    position: relative;
    width: 525px;
    height: 300px;
    background: var(--card-black);
    overflow: hidden;
    box-shadow: 0 14px 30px rgba(0,0,0,0.45);
  }

  /* Contact side */
  .card--contact {
    background: linear-gradient(160deg, #1a1a1b 0%, var(--card-black) 55%);
  }
  .band {
    position: absolute;
    left: 0;
    width: 100%;
    height: 14px;
    background: var(--brand-red);
  }
  .band--top { top: 0; }
  .band--bottom { bottom: 0; }
  .contact-block {
    position: absolute;
    inset: 14px 0;
    display: flex;
    flex-direction: column;
    align-items: center;
    justify-content: center;
    text-align: center;
    color: var(--text-white);
  }
  .person-name { font-size: 17px; font-weight: 700; line-height: 1.2; }
  .person-title { font-size: 12px; color: var(--text-soft); margin-bottom: 18px; }
  .phone-list { list-style: none; font-size: 13px; line-height: 1.35; }
  .email { font-size: 13px; margin-top: 2px; }
  .services {
    font-size: 14px;
    margin-top: 32px;
    letter-spacing: 0.1px;
  }

  /* Brand side */
  .card--brand {
    background: radial-gradient(ellipse at 50% 40%, var(--card-glow) 0%, var(--card-black) 62%);
  }
  .edge-tab {
    position: absolute;
    width: 30px;
    height: 40px;
    background: var(--brand-red);
    border-left: 5px solid var(--steel-grey);
  }
  .edge-tab--left { left: 0; top: 150px; border-left: none; border-right: 5px solid var(--steel-grey); width: 28px; height: 40px; }
  .edge-tab--right { right: 0; top: 20px; }
  .brand-name {
    position: absolute;
    left: 0; right: 0;
    top: 118px;
    display: flex;
    align-items: center;
    justify-content: center;
    gap: 12px;
    color: var(--steel-grey);
    font-size: 24px;
    font-weight: 700;
    letter-spacing: 1px;
  }
  .brand-mark {
    width: 14px;
    height: 14px;
    background: var(--brand-red);
  }
</style>
</head>
<body>
  <main class="stage">
    <section class="card card--contact" aria-label="Business card, contact side">
      <div class="band band--top"></div>
      <div class="contact-block">
        <p class="person-name">Corey Halvorsen</p>
        <p class="person-title">Area Manager</p>
        <ul class="phone-list">
          <li>(555) 410-2200</li>
          <li>(555) 418-7362</li>
          <li>(555) 410-2291</li>
        </ul>
        <p class="email">corey.halvorsen@brenwickcasing.com</p>
        <p class="services">Laydown Machine | Casing Crew | Mud Tool | Torque Turn</p>
      </div>
      <div class="band band--bottom"></div>
    </section>

    <section class="card card--brand" aria-label="Business card, brand side">
      <div class="edge-tab edge-tab--right"></div>
      <div class="edge-tab edge-tab--left"></div>
      <p class="brand-name"><span class="brand-mark"></span>Brenwick Casing Services</p>
    </section>
  </main>
</body>
</html>
```